Recruitment of Trellan Staffing for the UK market

I want a website for the UK market to attract businesses and companies to come to us for Philipine labour. We want an information site that gives all information on what we do and how we can recruit Philippine labour.
This is a recruitment site for companies to contact us with their requirements for skilled workers coming from the Philipines over to the UK to work.

Target Market(s)

Uk Companies and businesses who want Philipine skilled workers

Industry/Entity Type

REcruitment

Coding

Number of Pages Required

5+ page

Font styles to use
Sans Serif

Colors
0054AA
0677BA
7BADD7
CADEEF
E8F1F8
0094D4
00A9DD
6FCCEA
C7EBF8
E9F6FB
EE7325
F08F49
F5BC92
FAE3D3
FDF4ED
EB3D1F
EC4F4E
F09395
F8D3D4
FCEDEE

Requirements
Must have
• Look professional and corperate with drop down menus for Home ,about, services,articles. training , contact us
Nice to have
• Look at Velmora recruitment- https://velmorarecruitment.example.co.uk/. This is my current site - https://www.trellanstaffing.example.com/
Should not have
• Cartoons or silly pictures , needs to be corperate looking

```html
<!DOCTYPE html>
<html lang="en">
<head>
<meta charset="utf-8">
<title>Trellan Staffing – Skilled Philippine Workers for UK Companies</title>
<link rel="stylesheet" href="https://fonts.googleapis.com/css2?family=Outfit:wght@400;500;600;700&family=Nunito+Sans:wght@400;600&display=swap">
<style>
:root{
  --navy:#3f5fa5;
  --navy-dark:#4a65a8;
  --sky:#7badd7;
  --pale:#e8f1f8;
  --pale-2:#cadeef;
  --band:#c4d6ec;
  --red:#eb3d1f;
  --ink:#1c1c1c;
  --body:#4a4a4a;
  --white:#ffffff;
}
*{margin:0;padding:0;box-sizing:border-box}
html,body{width:1200px;height:4273px;overflow:hidden}
body{position:relative;background:var(--white);font-family:"Nunito Sans",sans-serif;color:var(--body)}
.abs{position:absolute}
h1,h2,h3,.brand{font-family:"Outfit",sans-serif;color:var(--ink)}
.btn{position:absolute;display:flex;align-items:center;justify-content:center;background:var(--red);color:var(--white);font-size:15px;border-radius:5px;font-family:"Nunito Sans",sans-serif}

/* header */
.site-header{position:absolute;left:0;top:0;width:1200px;height:100px;background:var(--white)}
.brand{position:absolute;left:113px;top:34px;font-size:26px;font-weight:700;color:var(--red);display:flex;align-items:center;gap:10px}
.brand .dot{width:14px;height:14px;background:var(--navy)}
.main-nav{position:absolute;top:43px;left:594px;display:flex;gap:33px;font-size:15px;color:var(--ink)}
.main-nav .active{position:relative}
.main-nav .active::after{content:"";position:absolute;left:0;right:0;bottom:-9px;height:3px;background:var(--red)}

/* hero */
.hero-photo{position:absolute;left:0;top:100px;width:1200px;height:590px}
.hero-title{position:absolute;left:0;top:255px;width:1200px;text-align:center;color:var(--white);font-size:46px;font-weight:600;line-height:60px}
.hero-btn{left:538px;top:464px;width:124px;height:38px}

/* about */
.about-title{left:113px;top:790px;font-size:34px;font-weight:600}
.about-text{left:113px;top:857px;width:489px;font-size:16px;line-height:29px;text-align:justify}
.photo{position:absolute}
.tile{position:absolute;background:var(--navy)}

/* contact row */
.contact-line{position:absolute;left:251px;top:1155px;width:640px;height:4px;background:var(--sky)}
.contact-icon{position:absolute;width:84px;height:84px;border-radius:50%;background:var(--pale);display:flex;align-items:center;justify-content:center}
.contact-text{position:absolute;font-size:23px;color:var(--ink);text-align:center;line-height:31px}
.social{position:absolute;width:42px;height:42px;border-radius:50%;background:var(--navy)}

/* working together */
.section-title{position:absolute;left:0;width:1200px;text-align:center;font-size:36px;font-weight:600}
.section-sub{position:absolute;left:0;width:1200px;text-align:center;font-size:16px;line-height:30px}
.card{position:absolute;top:1814px;width:287px;height:463px;background:var(--white);border-radius:8px;box-shadow:0 2px 10px rgba(40,60,110,.15)}
.card-icon{position:absolute;left:75px;top:-48px;width:136px;height:136px;border-radius:50%;background:var(--navy);display:flex;align-items:center;justify-content:center}
.card-head{position:absolute;left:0;top:100px;width:287px;height:71px;background:var(--band);border-radius:6px;display:flex;align-items:center;justify-content:center;font-family:"Outfit",sans-serif;font-weight:600;font-size:24px;color:var(--ink)}
.card-text{position:absolute;left:22px;top:211px;width:243px;text-align:center;font-size:16px;line-height:26px}
.card .btn{left:81px;top:394px;width:124px;height:40px}
.card.faded{opacity:.45}
.arrow-btn{position:absolute;width:60px;height:60px;border-radius:50%;background:var(--white);box-shadow:0 2px 8px rgba(0,0,0,.2);display:flex;align-items:center;justify-content:center}

/* skilled list */
.rule{position:absolute;background:var(--navy)}
.skill-title{left:606px;top:2477px;font-size:34px;font-weight:600}
.skill-text{left:606px;top:2543px;width:478px;font-size:16px;line-height:29px;text-align:justify}
.role{position:absolute;top:2883px;width:169px}
.role .pic{width:169px;height:151px}
.role p{margin-top:14px;text-align:center;font-size:19px;line-height:30px;color:var(--ink)}

/* sponsor/timeline */
.info-box{position:absolute;top:3345px;height:490px;border:3px solid var(--pale-2);background:var(--pale)}
.info-box h2{position:absolute;left:110px;top:40px;font-size:34px;font-weight:600}
.info-box .txt{position:absolute;left:110px;top:118px;width:463px;font-size:16px;line-height:29px}
.info-box .btn{top:423px;width:124px;height:42px}
.link{color:var(--navy);text-decoration:underline}

/* footer */
.foot-nav{position:absolute;left:113px;top:4070px;display:flex;gap:28px;font-size:15px;color:var(--ink)}
.map{position:absolute;left:689px;top:4000px;width:375px;height:175px;border-radius:10px}
.map-tag{position:absolute;left:932px;top:4006px;font-size:11px;color:var(--ink)}
.bottom-bar{position:absolute;left:0;top:4208px;width:1200px;height:65px;background:var(--navy-dark);color:var(--white);font-size:15px}
.bottom-bar .left{position:absolute;left:113px;top:22px}
.bottom-bar .right{position:absolute;right:118px;top:22px}
</style>
</head>
<body>

<header class="site-header">
  <div class="brand"><span class="dot"></span>Trellan Staffing</div>
  <nav class="main-nav">
    <span class="active">Home</span><span>About</span><span>Services</span><span>Articles</span><span>Training</span><span>Contact Us</span>
  </nav>
</header>

<svg class="hero-photo" viewBox="0 0 1200 590" role="img" aria-label="Photo of factory workers on a production floor under a blue overlay">
  <defs>
    <linearGradient id="heroFill" x1="0" y1="0" x2="1" y2="1">
      <stop offset="0" stop-color="#4f73b3"/><stop offset=".5" stop-color="#3d64a8"/><stop offset="1" stop-color="#2f5aa0"/>
    </linearGradient>
  </defs>
  <polygon points="0,0 1200,0 1200,590 0,590" fill="#a9c4e3"/>
  <polygon points="0,0 1200,0 1200,551 0,501" fill="url(#heroFill)"/>
  <polygon points="0,501 1200,551 1200,590 0,525" fill="#a9c4e3"/>
  <polygon points="0,525 1200,590 0,590" fill="#ffffff"/>
</svg>
<h1 class="hero-title">Recruiting And Placing Skilled<br>Philippine Workers Into UK<br>Companies</h1>
<span class="btn hero-btn">Get Started</span>

<h2 class="abs about-title">What The Business Is About</h2>
<p class="abs about-text">We source skilled workers directly from the Philippines to work in the UK. With offices , training locations and specialist recruiters we can find the highest quality individuals to add value and resources to any UK business. We delivery quality based on vast experience over a number of years.</p>
<div class="tile" style="left:898px;top:823px;width:65px;height:40px"></div>
<div class="tile" style="left:773px;top:926px;width:64px;height:42px"></div>
<svg class="photo" style="left:661px;top:765px" width="230" height="153" role="img" aria-label="Photo of smiling workers in blue uniforms"><rect width="230" height="153" fill="#7f9ec7"/></svg>
<svg class="photo" style="left:842px;top:873px" width="230" height="153" role="img" aria-label="Photo of two workers in hard hats on site"><rect width="230" height="153" fill="#b9777a"/></svg>

<div class="contact-line"></div>
<div class="contact-icon" style="left:167px;top:1115px"><svg width="30" height="30" viewBox="0 0 24 24"><path d="M6.6 10.8a15 15 0 0 0 6.6 6.6l2.2-2.2c.3-.3.7-.4 1-.2 1.1.4 2.3.6 3.6.6.6 0 1 .4 1 1V20c0 .6-.4 1-1 1A17 17 0 0 1 3 4c0-.6.4-1 1-1h3.5c.6 0 1 .4 1 1 0 1.3.2 2.5.6 3.6.1.3 0 .7-.2 1z" fill="#111"/></svg></div>
<div class="contact-icon" style="left:529px;top:1115px"><svg width="32" height="24" viewBox="0 0 32 24"><rect width="32" height="24" rx="2" fill="#111"/><path d="M1 2l15 11L31 2" stroke="#e8f1f8" stroke-width="2" fill="none"/></svg></div>
<div class="contact-icon" style="left:891px;top:1115px"><svg width="24" height="32" viewBox="0 0 24 32"><path d="M12 0a12 12 0 0 0-12 12c0 9 12 20 12 20s12-11 12-20A12 12 0 0 0 12 0z" fill="#111"/><circle cx="12" cy="12" r="4.5" fill="#e8f1f8"/></svg></div>
<p class="contact-text" style="left:109px;top:1247px;width:200px">01632 960 418</p>
<p class="contact-text" style="left:371px;top:1247px;width:400px">sales@trellanstaffing.example.com</p>
<p class="contact-text" style="left:778px;top:1215px;width:320px">Larkfield Gardens,<br>Ashby Marsh AB12 3<br>United Kingdom</p>
<span class="social" style="left:494px;top:1365px"></span>
<span class="social" style="left:550px;top:1365px"></span>
<span class="social" style="left:606px;top:1365px"></span>
<span class="social" style="left:665px;top:1365px"></span>

<svg class="abs" style="left:0;top:1502px" width="1200" height="600"><polygon points="0,0 1200,92 1200,600 0,600" fill="#e8f1f8"/></svg>
<h2 class="section-title" style="top:1615px">Working Together</h2>
<p class="section-sub" style="top:1678px">We recruit the finest talent available with our dedicated 200 strong team. Our centres are highlighted<br>in red dots on the map.</p>

<div class="card" style="left:113px">
  <div class="card-icon"><svg width="60" height="60" viewBox="0 0 60 60" fill="none" stroke="#fff" stroke-width="2.5"><rect x="14" y="24" width="26" height="20"/><path d="M14 24l13-9 13 9"/><circle cx="45" cy="17" r="7"/><path d="M6 50h26l10-6"/></svg></div>
  <div class="card-head">What we do</div>
  <p class="card-text">Our company has been established in the Philippines for over 20 years. We have mainly been recruiting philippine workers for the off shore industry in asia but since brexit and the new...</p>
  <span class="btn">Learn More</span>
</div>
<div class="card" style="left:428px">
  <div class="card-icon"><svg width="60" height="60" viewBox="0 0 60 60" fill="none" stroke="#fff" stroke-width="2.5"><circle cx="32" cy="22" r="12"/><circle cx="32" cy="22" r="5"/><path d="M8 46h14l8 4 16-8"/><rect x="4" y="40" width="6" height="14"/></svg></div>
  <div class="card-head">How we help</div>
  <p class="card-text">We work with companies to find skilled workers that meet the UK requirements for Visas and work permits. We guide you through the whole process and deliver highly trained people that add...</p>
  <span class="btn">Learn More</span>
</div>
<div class="card" style="left:742px">
  <div class="card-icon"><svg width="60" height="60" viewBox="0 0 60 60" fill="none" stroke="#fff" stroke-width="2.5"><path d="M30 12a13 13 0 0 0-8 23v6h16v-6a13 13 0 0 0-8-23z"/><path d="M24 46h12M26 51h8M8 26h5M47 26h5M14 10l4 4M46 10l-4 4"/></svg></div>
  <div class="card-head">Where to start</div>
  <p class="card-text">We need to know what your issues are and how we can understand the personal you require , over what time frame and the number of employees you need. Once this is estabilished we start...</p>
  <span class="btn">Learn More</span>
</div>
<div class="card faded" style="left:1057px">
  <div class="card-icon"><svg width="60" height="60" viewBox="0 0 24 24"><path d="M6.6 10.8a15 15 0 0 0 6.6 6.6l2.2-2.2c.3-.3.7-.4 1-.2 1.1.4 2.3.6 3.6.6.6 0 1 .4 1 1V20c0 .6-.4 1-1 1A17 17 0 0 1 3 4c0-.6.4-1 1-1h3.5c.6 0 1 .4 1 1 0 1.3.2 2.5.6 3.6.1.3 0 .7-.2 1z" fill="none" stroke="#fff" stroke-width="1.2"/></svg></div>
  <div class="card-head">Contact Us</div>
  <p class="card-text">contact us with your requirements, these may be care workers, pipe fitters, cabinet makers, medical staff from the UK list of required skills, extensive</p>
  <span class="btn">Learn More</span>
</div>
<div class="arrow-btn" style="left:1085px;top:1992px"><svg width="16" height="24" viewBox="0 0 16 24"><path d="M3 2l10 10L3 22" stroke="#3f5fa5" stroke-width="3" fill="none"/></svg></div>

<div class="rule" style="left:233px;top:2277px;width:3px;height:180px"></div>
<div class="rule" style="left:0;top:2569px;width:113px;height:3px"></div>
<svg class="photo" style="left:113px;top:2457px" width="458" height="340" role="img" aria-label="Photo of construction workers in hard hats and hi-vis vests"><rect width="458" height="340" fill="#8a7a66"/></svg>
<h2 class="abs skill-title">UK Skilled Workers List</h2>
<p class="abs skill-text">The UK government since brexit have developed a new system based on points (similar to Australia) when recruiting from outside of the UK. Previuosly EU citizens could work in the UK without any extensive documentation or clarification of skills. This has all changed. Overseas recruitment must now focus on skills that are currently short in the UK. The list is extensive and is constandly being reviewed.</p>
<span class="btn" style="left:606px;top:2769px;width:121px;height:41px">Read More</span>

<div class="role" style="left:20px"><svg class="pic" role="img" aria-label="Photo of a civil engineer on a building site"><rect width="169" height="151" fill="#7f98b8"/></svg><p>Civil Engineer</p></div>
<div class="role" style="left:217px"><svg class="pic" role="img" aria-label="Photo of lorries on a highway at speed"><rect width="169" height="151" fill="#9a8e6e"/></svg><p>Highways<br>Engineer</p></div>
<div class="role" style="left:413px"><svg class="pic" role="img" aria-label="Photo of engineers at a petroleum refinery at sunset"><rect width="169" height="151" fill="#a06a3a"/></svg><p>Petroleum<br>Engineer</p></div>
<div class="role" style="left:612px"><svg class="pic" role="img" aria-label="Photo of public health workers in a clinic"><rect width="169" height="151" fill="#a7b8c9"/></svg><p>Public Health<br>Engineer</p></div>
<div class="role" style="left:810px"><svg class="pic" role="img" aria-label="Photo of a site engineer with a clipboard"><rect width="169" height="151" fill="#b7b3a6"/></svg><p>Site Engineer</p></div>
<div class="role" style="left:1008px"><svg class="pic" role="img" aria-label="Photo of a structural engineer reviewing drawings"><rect width="169" height="151" fill="#b8bcc3"/></svg><p>Structural<br>Engineer</p></div>
<div class="arrow-btn" style="left:13px;top:2933px"><svg width="16" height="24" viewBox="0 0 16 24"><path d="M13 2L3 12l10 10" stroke="#3f5fa5" stroke-width="3" fill="none"/></svg></div>
<div class="arrow-btn" style="left:1120px;top:2933px"><svg width="16" height="24" viewBox="0 0 16 24"><path d="M3 2l10 10L3 22" stroke="#3f5fa5" stroke-width="3" fill="none"/></svg></div>
<span class="btn" style="left:538px;top:3149px;width:123px;height:41px">View More</span>

<svg class="abs" style="left:0;top:3237px" width="1200" height="971"><polygon points="0,0 1200,92 1200,971 0,971" fill="#e8f1f8"/></svg>
<section class="info-box" style="left:0;width:600px">
  <h2>Sponsor Licence</h2>
  <p class="txt" style="text-align:justify">If you have areas of your business that meet the entry requirements of skilled labour your next step is to gain a sponsor licence for your business. There are different types of licences depending on the size of the business.<br>All information can be found here-<br><span class="link">https://www.sponsorlicence.example.org/apply</span><br>It si estimated that the whole process takes between 20 and 30 minutes and approximatly 6 weeks thereafter to be approved.</p>
  <span class="btn" style="left:113px">Learn More</span>
</section>
<section class="info-box" style="left:606px;width:594px">
  <h2 style="left:15px">Recruitment Timeline</h2>
  <p class="txt" style="left:17px;width:470px">&nbsp; Brief us on the job profiles – this is passed on to our teams in the Philippines.<br><br>&nbsp;- Our teams in the Philippines source suitable candidates, documentation required for each candidate will be checked and vetted by the Recruitment Team. Once deemed qualified, they will now be assessed by their Technical Interviewer .<br>&nbsp;- The candidates must provide a police check as pre-requisite for recruitment process to proceed</p>
  <span class="btn" style="left:17px">Learn More</span>
</section>

<div class="brand" style="top:3990px">
  <span class="dot"></span>Trellan Staffing
</div>
<nav class="foot-nav"><span>Home</span><span>About</span><span>Services</span><span>Articles</span><span>Training</span><span>Contact Us</span></nav>
<span class="social" style="left:113px;top:4127px"></span>
<span class="social" style="left:171px;top:4127px"></span>
<span class="social" style="left:229px;top:4127px"></span>
<span class="social" style="left:286px;top:4127px"></span>
<div class="rule" style="left:937px;top:3921px;width:2px;height:79px"></div>
<div class="rule" style="left:1064px;top:4061px;width:136px;height:2px"></div>
<svg class="map" role="img" aria-label="Map of the Philippines with office locations marked"><rect width="375" height="175" rx="10" fill="#9fb9ec"/></svg>
<span class="map-tag">Click Here To See Map</span>

<footer class="bottom-bar">
  <span class="left">Privacy Policy &nbsp;|&nbsp; Terms &amp; Conditions</span>
  <span class="right">© Copyrights 2023 Trellan Staffing | All Rights Reserved</span>
</footer>

</body>
</html>
```